mothers day ad for martial arts school

I am looking to have a nice flyer/handout to promote my martial arts school. It is for our promotion of "mom's train free" for mothers day in May. I would like an ad that would inspire a mother to learn self defense and to improve their fitness. It can have pictures but not necessarily a requirement. Pictures don't have to be of a lady in a martial arts uniform. It may be better if they are not. It also doesn't have to be standard sheet of paper size, as these are going to be handouts the size can be smaller. I would like our Copper Vale logo on the flyer.

Target Market(s)

mothers that hadn't thought about martial arts before but would be convinced to try it

Industry/Entity Type

School

Requirements
Must have
• text, photos that would appeal to and encourage a mother to try a self defense/fitness class
Nice to have
• our logo and text and possibly pictures that would inspire a mother to join a martial arts class

```html
<!DOCTYPE html>
<html lang="en">
<head>
<meta charset="utf-8">
<title>Mothers Train Free – Copper Vale Ascend Martial Arts</title>
<link href="https://fonts.googleapis.com/css2?family=Roboto:wght@300;400;500;700&display=swap" rel="stylesheet">
<style>
  :root {
    --backdrop: #e6e7e9;
    --paper: #ffffff;
    --brand-red: #d21f30;
    --brand-red-dark: #8e1620;
    --ink: #222222;
    --charcoal: #262626;
    --on-dark: #ffffff;
  }
  * { margin: 0; padding: 0; box-sizing: border-box; }
  html, body {
    width: 1200px; height: 856px; overflow: hidden;
    background: var(--backdrop);
    font-family: "Roboto", Arial, sans-serif;
  }
  .flyer {
    position: absolute; left: 282px; top: 18px;
    width: 636px; height: 820px;
    background: var(--paper);
    overflow: hidden;
  }
  .brand {
    position: absolute; left: 0; top: 52px; width: 100%;
    text-align: center; color: var(--ink); font-weight: 500;
  }
  .brand__prefix { font-size: 17px; letter-spacing: 5px; }
  .brand__name { font-size: 66px; line-height: 1; letter-spacing: 4px; margin: 4px 0 2px; }
  .brand__suffix { font-size: 17px; letter-spacing: 6px; }
  .hero-photo {
    position: absolute; left: 0; top: 240px; width: 636px; height: 455px;
    background:
      radial-gradient(ellipse at 38% 45%, #b98f86 0%, rgba(185,143,134,0) 45%),
      linear-gradient(100deg, #c9a79a 0%, #d9b9a6 35%, #cbb2b8 65%, #a79aa8 100%);
  }
  .shapes { position: absolute; left: 0; top: 0; }
  .offer {
    position: absolute; left: 361px; top: 220px; width: 231px;
    color: var(--on-dark); text-align: center; font-weight: 700; line-height: 1.18;
  }
  .offer__big { font-size: 42px; }
  .offer__mid { font-size: 37px; }
  .offer__days { font-size: 40px; }
  .offer__terms { font-size: 22px; font-weight: 400; line-height: 1.2; margin-top: 2px; }
  .offer__terms sup { font-size: 13px; }
  .benefits {
    position: absolute; left: 442px; top: 598px;
    list-style: none; color: var(--on-dark);
    font-size: 19px; font-weight: 700; line-height: 26px;
  }
  .contact-bar {
    position: absolute; left: 0; top: 695px; width: 636px; height: 45px;
    background: var(--charcoal); color: var(--on-dark);
    font-size: 29px; font-weight: 300; text-align: center; line-height: 45px;
    word-spacing: 3px;
  }
  .address {
    position: absolute; left: 0; top: 776px; width: 636px;
    text-align: center; color: var(--ink); font-size: 17px;
  }
</style>
</head>
<body>
  <main class="flyer">
    <header class="brand">
      <div class="brand__prefix">COPPER VALE</div>
      <div class="brand__name">ASCEND</div>
      <div class="brand__suffix">MARTIAL ARTS</div>
    </header>

    <div class="hero-photo" role="img" aria-label="Photo of a determined woman raising her fist in a bright training space"></div>

    <svg class="shapes" width="636" height="820" viewBox="0 0 636 820" aria-hidden="true">
      <polygon points="248,240 361,206 361,240" fill="var(--brand-red-dark)"/>
      <polygon points="361,206 592,206 592,525 361,571" fill="var(--brand-red)"/>
      <polygon points="417,560 592,525 592,695 417,695" fill="var(--charcoal)"/>
    </svg>

    <section class="offer">
      <div class="offer__big">MOTHERS</div>
      <div class="offer__big">TRAIN</div>
      <div class="offer__mid">FREE FOR</div>
      <div class="offer__days">30 DAYS</div>
      <div class="offer__terms">WHEN YOU START<br>BY MAY 31<sup>ST</sup>!</div>
    </section>

    <ul class="benefits">
      <li>*FEEL STRONG</li>
      <li>*LOOK GOOD</li>
      <li>*GET STRONG</li>
      <li>*FEEL SAFE</li>
    </ul>

    <div class="contact-bar">CONTACT US NOW &nbsp;123456789</div>
    <p class="address">YOUR WEBSITE OR YOUR ADDRESS</p>
  </main>
</body>
</html>
```